Need Web Design for Business Process Outsourcing Company (Quorvane)

Quorvane is a business process outsourcing company. Need a simple site similar to http://www.tallowbrinkhire.com/ but with a more professional and credible look. New to the process; not sure where to start and comparing my options. Please let me know what my options are if I choose to go with you. Logo is attached for your reference. Please use same colorway

Reason: I want the final product to be coded. Please confirm you will be able to code final design.

Industry/Entity Type

Business

Coding

Coded - Design and coding required

```html
<!DOCTYPE html>
<html lang="en">
<head>
<meta charset="utf-8">
<title>Quorvane Services — Business Process Outsourcing</title>
<link rel="stylesheet" href="https://fonts.googleapis.com/css2?family=Open+Sans:wght@400;600;700&family=Roboto+Condensed:wght@400;700&family=Roboto:wght@400;500&display=swap">
<style>
:root{
  --blue:#1b8fd8;
  --blue-deep:#0f6db0;
  --navy:#1b3f66;
  --ink:#333a42;
  --muted:#6b7278;
  --line:#dcdfe2;
  --paper:#ffffff;
  --footer:#f3f4f5;
  --nav-active:#555b61;
}
*{box-sizing:border-box;margin:0;padding:0}
html,body{width:1200px;height:2844px;overflow:hidden}
body{position:relative;background:var(--paper);font-family:"Open Sans",Arial,sans-serif;color:var(--ink)}
.abs{position:absolute}

/* header */
.site-header{left:0;top:0;width:1200px;height:131px;background:var(--paper)}
.brand{display:flex;align-items:center;gap:12px}
.brand-square{width:48px;height:48px;background:var(--blue)}
.brand-name{font-family:"Open Sans",Arial,sans-serif;font-weight:700;font-size:34px;color:var(--navy);letter-spacing:-.5px;line-height:1;white-space:nowrap}
.header-brand{left:99px;top:38px}
.call{left:788px;top:40px;display:flex;align-items:center;gap:10px;white-space:nowrap}
.call-icon{width:32px;height:32px;border:2px solid var(--blue);border-radius:50%;display:flex;align-items:center;justify-content:center}
.call-text{font-family:"Roboto",Arial,sans-serif;line-height:1.25}
.call-text .label{color:var(--blue);font-size:15px}
.call-text .number{color:var(--ink);font-size:16px}
.socials{display:flex;gap:7px}
.header-socials{left:967px;top:47px}
.social-dot{width:30px;height:30px;border:2px solid var(--blue);border-radius:50%}

/* nav */
.main-nav{left:0;top:131px;width:1200px;height:49px;background:var(--blue)}
.main-nav ul{list-style:none;display:flex;margin-left:99px;height:49px}
.main-nav li{font-family:"Roboto",Arial,sans-serif;font-size:13px;color:#fff;padding:0 22px;line-height:49px;text-transform:uppercase;white-space:nowrap}
.main-nav li.active{background:var(--nav-active)}

/* hero */
.hero{left:0;top:180px;width:1200px;height:514px;overflow:hidden}
.hero-photo{width:100%;height:100%;background:linear-gradient(120deg,#4a3c34 0%,#8b8a88 35%,#b9bdc0 60%,#6f7378 100%)}
.hero-curve{left:0;bottom:0}
.hero-card{left:705px;top:154px;width:368px;height:200px;background:rgba(27,143,216,.92);padding:16px 24px}
.hero-card h1{font-family:"Roboto Condensed",Arial,sans-serif;font-weight:700;color:#fff;line-height:1.05}
.hero-card .h1-top{font-size:42px;display:block}
.hero-card .h1-sub{font-size:31px;display:block}
.btn-more{display:inline-block;margin-top:14px;background:var(--navy);color:#fff;font-family:"Roboto",Arial,sans-serif;font-size:14px;padding:10px 20px;text-transform:uppercase}
.dots{display:flex;gap:8px;margin-top:16px;align-items:center}
.dots span{width:11px;height:11px;border-radius:50%;background:#fff}
.dots span.on{width:17px;height:17px;border:3px solid #fff;background:var(--blue);box-shadow:inset 0 0 0 2px #fff}

/* section titles */
.section-title{left:0;width:1200px;text-align:center;font-family:"Roboto Condensed",Arial,sans-serif;font-weight:400;font-size:33px;color:var(--ink);text-transform:uppercase}
.title-rule{left:570px;width:60px;height:3px;background:var(--blue)}

/* services */
.service{width:230px;text-align:center}
.service-icon{width:100px;height:100px;border:2px solid var(--ink);border-radius:50%;margin:0 auto;display:flex;align-items:center;justify-content:center}
.service h3{margin-top:28px;font-family:"Roboto",Arial,sans-serif;font-weight:400;font-size:15px;text-transform:uppercase;color:var(--ink)}
.service p{margin-top:8px;font-size:12px;line-height:20px;color:var(--muted)}
.service .chev{margin-top:8px}

/* what we do */
.what-band{left:0;top:1180px;width:1200px;height:464px;background:linear-gradient(90deg,#3c97e4 0%,#2f8fe0 55%,#4fa6ea 100%)}
.laptop-art{left:190px;top:93px;width:437px;height:276px;background:linear-gradient(160deg,#3a4656 0%,#8a9cb0 50%,#c6ccd2 100%);border-radius:6px}
.what-title{left:682px;top:66px;font-family:"Roboto Condensed",Arial,sans-serif;font-weight:700;font-size:28px;color:#fff}
.feature{left:678px;display:flex;gap:20px;width:400px}
.feature-icon{width:64px;height:64px;flex:none;border-radius:50%;background:#fff;border:4px solid rgba(255,255,255,.5);box-shadow:0 0 0 3px var(--blue) inset;display:flex;align-items:center;justify-content:center}
.feature h4{font-family:"Roboto",Arial,sans-serif;font-weight:500;font-size:16px;color:#fff;text-transform:uppercase;margin-top:2px}
.feature p{margin-top:6px;font-size:12px;line-height:19px;color:#fff}

/* blog */
.blog-card{top:1794px;width:313px;height:309px;background:#f7f8f8;box-shadow:0 1px 3px rgba(0,0,0,.15)}
.blog-image{width:313px;height:174px}
.blog-body{padding:18px 15px}
.blog-body h5{font-family:"Roboto",Arial,sans-serif;font-weight:400;font-size:15px;color:var(--ink)}
.blog-meta{margin-top:10px;font-size:12px;color:var(--ink);display:flex;align-items:center;gap:5px}
.blog-body p{margin-top:10px;font-size:12px;line-height:19px;color:var(--muted)}

/* testimonials */
.testimonial-band{left:0;top:2187px;width:1200px;height:298px;background:linear-gradient(120deg,#0e5f9e 0%,#1a74b8 50%,#12649f 100%)}
.testimonial-title{left:0;top:56px;width:1200px;text-align:center;font-family:"Roboto Condensed",Arial,sans-serif;font-weight:400;font-size:30px;color:#fff}
.testimonial-quote{left:210px;top:114px;width:780px;text-align:center;font-size:12px;line-height:21px;color:#fff}
.testimonial-name{left:0;top:197px;width:1200px;text-align:center;font-style:italic;font-size:15px;color:#fff}
.testimonial-dots{left:552px;top:253px;display:flex;gap:6px}
.testimonial-dots span{width:28px;height:3px;background:rgba(255,255,255,.35)}
.testimonial-dots span.on{background:#fff}

/* footer */
.site-footer{left:0;top:2485px;width:1200px;height:308px;background:var(--footer)}
.footer-brand{left:99px;top:140px}
.footer-brand .brand-name{font-size:30px}
.footer-brand .brand-square{width:42px;height:42px}
.footer-heading{font-family:"Roboto",Arial,sans-serif;font-weight:500;font-size:17px;color:var(--ink);text-transform:uppercase}
.enquiry{left:350px;top:62px}
.field{position:absolute;background:#fff;border:1px solid var(--line);font-size:11px;color:var(--ink);padding:10px 12px}
.btn-submit{position:absolute;left:0;width:106px;height:33px;border:2px solid var(--blue);color:var(--blue);font-family:"Roboto",Arial,sans-serif;font-weight:500;font-size:15px;text-align:center;line-height:29px;background:#fff}
.contacts{left:707px;top:55px}
.contact-row{display:flex;gap:10px;font-size:13px;color:var(--muted);line-height:19px;margin-top:12px}
.contact-row svg{flex:none;margin-top:3px}
.footer-socials{display:flex;gap:4px;margin-top:14px}
.footer-socials span{width:22px;height:22px;border-radius:50%;background:var(--blue)}
.footer-socials span:last-child{background:#d53a2f}
.quick-links{left:986px;top:55px}
.quick-links ul{list-style:none;margin-top:14px}
.quick-links li{font-size:11.5px;color:var(--ink);line-height:22px}
.copyright{left:0;top:2793px;width:1200px;height:51px;border-top:1px solid var(--line);text-align:center;font-size:11px;color:var(--muted);line-height:50px;background:#fff}
</style>
</head>
<body>

<header class="site-header abs">
  <div class="brand header-brand abs">
    <span class="brand-square"></span>
    <span class="brand-name">Quorvane</span>
  </div>
  <div class="call abs">
    <span class="call-icon">
      <svg width="15" height="15" viewBox="0 0 24 24"><path d="M6.6 10.8a15.1 15.1 0 0 0 6.6 6.6l2.2-2.2c.3-.3.7-.4 1-.2 1.1.4 2.3.6 3.6.6.6 0 1 .4 1 1V20c0 .6-.4 1-1 1A17 17 0 0 1 3 4c0-.6.4-1 1-1h3.5c.6 0 1 .4 1 1 0 1.3.2 2.5.6 3.6.1.3 0 .7-.2 1z" fill="none" stroke="#1b8fd8" stroke-width="2"/></svg>
    </span>
    <div class="call-text">
      <div class="label">Call Us</div>
      <div class="number">+(555) 410-2280</div>
    </div>
  </div>
  <div class="socials header-socials abs">
    <span class="social-dot"></span><span class="social-dot"></span><span class="social-dot"></span><span class="social-dot" style="border-color:#d53a2f"></span>
  </div>
</header>

<nav class="main-nav abs">
  <ul>
    <li class="active">Home</li><li>Who We Are</li><li>Our Solutions</li><li>Our Strategy</li><li>Our Experience</li><li>Blog</li><li>Careers</li><li>Contact Us</li>
  </ul>
</nav>

<section class="hero abs">
  <div class="hero-photo" role="img" aria-label="Photo of a call centre agent with a headset taking notes beside a laptop"></div>
  <svg class="hero-curve abs" width="1200" height="60" viewBox="0 0 1200 60">
    <path d="M0 10 Q600 80 1200 10 L1200 60 L0 60 Z" fill="#fff"/>
    <path d="M0 10 Q600 80 1200 10" fill="none" stroke="#1b8fd8" stroke-width="3"/>
  </svg>
  <div class="hero-card abs">
    <h1><span class="h1-top">BPO BUSINESS</span><span class="h1-sub">PROCESS OUTSOURCING</span></h1>
    <span class="btn-more">More Information</span>
    <div class="dots"><span class="on"></span><span></span><span></span><span></span></div>
  </div>
</section>

<h2 class="section-title abs" style="top:766px">Outsourcing Services</h2>
<div class="title-rule abs" style="top:818px"></div>

<div class="service abs" style="left:90px;top:870px">
  <div class="service-icon"><svg width="40" height="40" viewBox="0 0 24 24"><path d="M4 14v-2a8 8 0 0 1 16 0v2" fill="none" stroke="#333a42" stroke-width="2.2"/><rect x="3" y="13" width="5" height="7" rx="2" fill="#333a42"/><rect x="16" y="13" width="5" height="7" rx="2" fill="#333a42"/></svg></div>
  <h3>Customer Service</h3>
  <p>Sed ut perspiciatis unde omnis iste natus error sit voluptatem accusantium dolor-emque laudantium, totam rem</p>
  <svg class="chev" width="14" height="14" viewBox="0 0 14 14"><path d="M2 2l5 4 5-4M2 7l5 4 5-4" fill="none" stroke="#333a42" stroke-width="1.5"/></svg>
</div>
<div class="service abs" style="left:355px;top:870px">
  <div class="service-icon"><svg width="40" height="40" viewBox="0 0 24 24"><path d="M2 4h3l2.5 11h11L21 7H7" fill="none" stroke="#333a42" stroke-width="2"/><rect x="7" y="8" width="12" height="6" fill="#333a42"/><circle cx="9" cy="19" r="1.8" fill="#333a42"/><circle cx="17" cy="19" r="1.8" fill="#333a42"/></svg></div>
  <h3>Ecommerce</h3>
  <p>Sed ut perspiciatis unde omnis iste natus error sit voluptatem accusantium dolor-emque laudantium, totam rem</p>
  <svg class="chev" width="14" height="14" viewBox="0 0 14 14"><path d="M2 2l5 4 5-4M2 7l5 4 5-4" fill="none" stroke="#333a42" stroke-width="1.5"/></svg>
</div>
<div class="service abs" style="left:620px;top:870px">
  <div class="service-icon"><svg width="40" height="40" viewBox="0 0 24 24"><rect x="2" y="3" width="20" height="14" rx="1.5" fill="#333a42"/><rect x="4" y="5" width="16" height="10" fill="#fff"/><path d="M9 17l-1 4h8l-1-4" fill="#333a42"/></svg></div>
  <h3>IT Solutions</h3>
  <p>Sed ut perspiciatis unde omnis iste natus error sit voluptatem accusantium dolor-emque laudantium, totam rem</p>
  <svg class="chev" width="14" height="14" viewBox="0 0 14 14"><path d="M2 2l5 4 5-4M2 7l5 4 5-4" fill="none" stroke="#333a42" stroke-width="1.5"/></svg>
</div>
<div class="service abs" style="left:878px;top:870px">
  <div class="service-icon"><svg width="44" height="40" viewBox="0 0 28 24"><circle cx="14" cy="7" r="4" fill="#333a42"/><circle cx="6" cy="9" r="3" fill="#333a42"/><circle cx="22" cy="9" r="3" fill="#333a42"/><path d="M7 21a7 7 0 0 1 14 0z" fill="#333a42"/><path d="M1 21a5 5 0 0 1 6-5v5zM27 21a5 5 0 0 0-6-5v5z" fill="#333a42"/></svg></div>
  <h3>Human Resources</h3>
  <p>Sed ut perspiciatis unde omnis iste natus error sit voluptatem accusantium dolor-emque laudantium, totam rem</p>
  <svg class="chev" width="14" height="14" viewBox="0 0 14 14"><path d="M2 2l5 4 5-4M2 7l5 4 5-4" fill="none" stroke="#333a42" stroke-width="1.5"/></svg>
</div>

<section class="what-band abs" role="img" aria-label="Blue tinted office skyline backdrop">
  <div class="laptop-art abs" role="img" aria-label="Laptop showing a businessman touching a network of connected people icons"></div>
  <h2 class="what-title abs">WHAT WE DO</h2>
  <div class="feature abs" style="top:138px">
    <span class="feature-icon"><svg width="26" height="26" viewBox="0 0 24 24"><path d="M12 2a10 10 0 1 0 10 10H12z" fill="#1b8fd8"/><path d="M14 0v10h10A10 10 0 0 0 14 0z" fill="#1b8fd8"/></svg></span>
    <div><h4>Reinventing Services</h4><p>Lorem ipsum dolor sit amet, consectetur adipiscing<br>elit, sed do eiusmod tempor incididunt</p></div>
  </div>
  <div class="feature abs" style="top:233px">
    <span class="feature-icon"><svg width="22" height="26" viewBox="0 0 20 24"><rect x="2" y="1" width="16" height="22" fill="none" stroke="#1b8fd8" stroke-width="2"/><path d="M6 6h3M11 6h3M6 11h3M11 11h3M6 16h3M11 16h3" stroke="#1b8fd8" stroke-width="2"/></svg></span>
    <div><h4>Our Facilities</h4><p>Lorem ipsum dolor sit amet, consectetur adipiscing<br>elit, sed do eiusmod tempor incididunt</p></div>
  </div>
  <div class="feature abs" style="top:328px">
    <span class="feature-icon"><svg width="24" height="24" viewBox="0 0 24 24"><circle cx="12" cy="8" r="5" fill="#1b8fd8"/><path d="M3 23a9 9 0 0 1 18 0z" fill="#1b8fd8"/></svg></span>
    <div><h4>Our People</h4><p>Lorem ipsum dolor sit amet, consectetur adipiscing<br>elit, sed do eiusmod tempor incididunt</p></div>
  </div>
</section>

<h2 class="section-title abs" style="top:1702px">Latest Blog</h2>
<div class="title-rule abs" style="top:1752px"></div>

<article class="blog-card abs" style="left:99px">
  <div class="blog-image" role="img" aria-label="Man facing a chalkboard wall of SEO sketches" style="background:linear-gradient(160deg,#2c2c2c,#6a6a6a 60%,#3a3a3a)"></div>
  <div class="blog-body">
    <h5>Nemo enim ipsam voluptatem</h5>
    <div class="blog-meta"><svg width="11" height="11" viewBox="0 0 12 12"><circle cx="6" cy="6" r="5" fill="none" stroke="#333a42" stroke-width="1.5"/><path d="M6 3v3h2" fill="none" stroke="#333a42" stroke-width="1.3"/></svg>3 minutes ago, 0 comments</div>
    <p>Lorem ipsum dolor sit amet, consectetur adipiscing elit, sed do eiusmod tempor ncididunt</p>
  </div>
</article>
<article class="blog-card abs" style="left:445px">
  <div class="blog-image" role="img" aria-label="Woman seated at a desk in a bright open office" style="background:linear-gradient(160deg,#cfc5b6,#a48c70 50%,#6b5a48)"></div>
  <div class="blog-body">
    <h5>Nemo enim ipsam voluptatem</h5>
    <div class="blog-meta"><svg width="11" height="11" viewBox="0 0 12 12"><circle cx="6" cy="6" r="5" fill="none" stroke="#333a42" stroke-width="1.5"/><path d="M6 3v3h2" fill="none" stroke="#333a42" stroke-width="1.3"/></svg>3 minutes ago, 0 comments</div>
    <p>Lorem ipsum dolor sit amet, consectetur adipiscing elit, sed do eiusmod tempor ncididunt</p>
  </div>
</article>
<article class="blog-card abs" style="left:789px">
  <div class="blog-image" role="img" aria-label="Businessman touching a glowing digital world map" style="background:linear-gradient(160deg,#1d3550,#4d7a9e 55%,#a9c0d2)"></div>
  <div class="blog-body">
    <h5>Nemo enim ipsam voluptatem</h5>
    <div class="blog-meta"><svg width="11" height="11" viewBox="0 0 12 12"><circle cx="6" cy="6" r="5" fill="none" stroke="#333a42" stroke-width="1.5"/><path d="M6 3v3h2" fill="none" stroke="#333a42" stroke-width="1.3"/></svg>3 minutes ago, 0 comments</div>
    <p>Lorem ipsum dolor sit amet, consectetur adipiscing elit, sed do eiusmod tempor ncididunt</p>
  </div>
</article>

<section class="testimonial-band abs" role="img" aria-label="Blue tinted glass building backdrop">
  <h2 class="testimonial-title abs">TESTIMONIALS</h2>
  <p class="testimonial-quote abs">“ Sed ut perspiciatis unde omnis iste natus error sit voluptatem accusantium doloremque laudantium, totam rem aperiam, eaque ipsa quae ab illo inventore veritatis et quasi architecto beatae vitae dicta sunt explicabo. Nemo enim ipsam voluptatem quia voluptas sit aspernatur aut odit aut fugit, sed quia consequuntur magni dolores eos qui ratione voluptatem</p>
  <p class="testimonial-name abs">Marion Keddle – Quorvane</p>
  <div class="testimonial-dots abs"><span class="on"></span><span></span><span></span></div>
</section>

<footer class="site-footer abs">
  <div class="brand footer-brand abs">
    <span class="brand-square"></span>
    <span class="brand-name">Quorvane</span>
  </div>
  <div class="enquiry abs">
    <h3 class="footer-heading">Quick Enquiry</h3>
    <div style="position:relative;width:300px;height:260px">
      <div class="field" style="left:0;top:22px;width:144px;height:38px">Name</div>
      <div class="field" style="left:153px;top:22px;width:147px;height:38px">Phone</div>
      <div class="field" style="left:0;top:68px;width:300px;height:64px">Message</div>
      <div class="btn-submit" style="top:144px">SUBMIT</div>
    </div>
  </div>
  <div class="contacts abs">
    <h3 class="footer-heading">Contacts Us</h3>
    <div class="contact-row"><svg width="12" height="14" viewBox="0 0 12 16"><path d="M6 1a5 5 0 0 0-5 5c0 4 5 9 5 9s5-5 5-9a5 5 0 0 0-5-5z" fill="none" stroke="#9aa0a5" stroke-width="1.5"/><circle cx="6" cy="6" r="1.8" fill="#9aa0a5"/></svg><span>Quorvane<br>no 10, Harlow Street, Westmere</span></div>
    <div class="contact-row"><svg width="12" height="12" viewBox="0 0 24 24"><path d="M6.6 10.8a15 15 0 0 0 6.6 6.6l2.2-2.2c.3-.3.7-.4 1-.2 1.1.4 2.3.6 3.6.6.6 0 1 .4 1 1V20c0 .6-.4 1-1 1A17 17 0 0 1 3 4c0-.6.4-1 1-1h3.5c.6 0 1 .4 1 1 0 1.3.2 2.5.6 3.6z" fill="#9aa0a5"/></svg><span>Phone: (555) 840-3170</span></div>
    <div class="contact-row"><svg width="13" height="10" viewBox="0 0 16 12"><rect x="1" y="1" width="14" height="10" fill="none" stroke="#9aa0a5" stroke-width="1.5"/><path d="M1 1l7 6 7-6" fill="none" stroke="#9aa0a5" stroke-width="1.5"/></svg><span>Email: info@quorvane.com</span></div>
    <div class="footer-socials"><span></span><span></span><span></span></div>
  </div>
  <nav class="quick-links abs">
    <h3 class="footer-heading">Quick Links</h3>
    <ul><li>Home</li><li>About</li><li>Services</li><li>Privacy Policy</li><li>Terms and Conditions</li><li>Sitemap</li></ul>
  </nav>
</footer>

<div class="copyright abs">©2015 - 2016 Quorvane., All Rights Reserved.</div>

</body>
</html>
```